The Q Collective Business Cards

We need a sleek looking business card for our real estate company. Looking for a clean, modern, eye catching design on a standard size business card.
Updates

No more submissions please! Thank you!

Target Market(s)

General Public/Real Estate Clients

Industry/Entity Type

Real Estate

Contact Information for Business Card

Cards will be customized for each agent.

Colors

Designer to choose only greyscale colors for use in the design.

Requirements
Must have
• Black, white, gray color pallet, Photo area for headshot on the front of the card

```html
<!DOCTYPE html>
<html lang="en">
<head>
<meta charset="utf-8">
<title>The Q Collective Business Cards</title>
<link href="https://fonts.googleapis.com/css2?family=Montserrat:wght@400;500&family=Roboto:wght@400;500&display=swap" rel="stylesheet">
<style>
  :root {
    --page: #2a2a2a;
    --card: #252525;
    --card-edge: #1d1d1d;
    --ink: #f2f2f2;
    --ink-soft: #d6d6d6;
    --rule: #bdbdbd;
    --strip: #8a8a8a;
    --photo-top: #6b5a50;
    --photo-bottom: #d9d6d3;
  }
  * { margin: 0; padding: 0; box-sizing: border-box; }
  html, body { width: 1200px; height: 1138px; overflow: hidden; }
  body {
    background: var(--page);
    font-family: "Roboto", Arial, sans-serif;
    color: var(--ink);
    position: relative;
  }
  .card {
    position: absolute;
    width: 620px;
    height: 374px;
    background: var(--card);
    border-radius: 14px;
    overflow: hidden;
    box-shadow: 0 4px 10px rgba(0,0,0,.45);
  }
  .card--back { left: 274px; top: 186px; }
  .card--front { left: 277px; top: 606px; height: 376px; }

  /* back */
  .brand-stack {
    position: absolute;
    left: 0; right: 0; top: 96px;
    text-align: center;
  }
  .brand-stack__name {
    font-family: "Montserrat", Arial, sans-serif;
    font-weight: 500;
    font-size: 30px;
    letter-spacing: 6px;
    color: var(--ink);
    text-transform: uppercase;
  }
  .brand-stack__tagline {
    display: inline-block;
    margin-top: 26px;
    padding: 5px 12px;
    background: #e9e9e9;
    color: #222;
    font-family: "Montserrat", Arial, sans-serif;
    font-weight: 500;
    font-size: 11px;
    letter-spacing: 2.4px;
  }
  .brokerage {
    position: absolute;
    left: 28px; top: 340px;
    font-family: "Montserrat", Arial, sans-serif;
    font-weight: 500;
    font-size: 11px;
    letter-spacing: .5px;
    color: var(--ink-soft);
    text-transform: uppercase;
  }

  /* front */
  .brand-line {
    position: absolute;
    left: 29px; top: 48px;
    font-family: "Montserrat", Arial, sans-serif;
    font-weight: 400;
    font-size: 31px;
    letter-spacing: 3px;
    color: var(--ink);
    text-transform: uppercase;
  }
  .brand-tagline {
    position: absolute;
    left: 29px; top: 108px;
    width: 330px;
    text-align: center;
    font-family: "Montserrat", Arial, sans-serif;
    font-size: 13px;
    letter-spacing: 6px;
    color: var(--ink-soft);
  }
  .headshot {
    position: absolute;
    left: 397px; top: 16px;
    width: 223px; height: 240px;
    background: linear-gradient(180deg, var(--photo-top) 0%, #8b766a 55%, var(--photo-bottom) 100%);
  }
  .agent { position: absolute; left: 29px; top: 192px; }
  .agent__name { font-family: "Montserrat", Arial, sans-serif; font-weight: 500; font-size: 24px; color: var(--ink); }
  .agent__title { font-size: 16px; color: var(--ink-soft); margin-top: 2px; }
  .divider {
    position: absolute;
    left: 28px; right: 0; top: 256px;
    height: 1px; background: var(--rule);
  }
  .contact { position: absolute; left: 29px; top: 280px; list-style: none; }
  .contact li {
    display: flex; align-items: center;
    height: 23.5px;
    font-size: 16px; color: var(--ink-soft);
  }
  .contact svg { width: 13px; height: 13px; margin-right: 17px; fill: var(--ink-soft); }
  .address {
    position: absolute;
    right: 31px; top: 303px;
    text-align: right;
    font-size: 16px; line-height: 23.5px;
    color: var(--ink-soft);
    font-style: normal;
  }
  .edge-strip {
    position: absolute;
    left: 0; right: 0; bottom: 0;
    height: 12px; background: var(--strip);
  }
</style>
</head>
<body>

<section class="card card--back" aria-label="Card back">
  <div class="brand-stack">
    <div class="brand-stack__name">The Q Collective</div>
    <div class="brand-stack__tagline">•REAL ESTATE TEAM•</div>
  </div>
  <div class="brokerage">Riverside Realty Partners</div>
</section>

<section class="card card--front" aria-label="Card front">
  <div class="brand-line">The Q Collective</div>
  <div class="brand-tagline">•REAL ESTATE TEAM•</div>

  <div class="headshot" role="img" aria-label="Agent headshot photo"></div>

  <div class="agent">
    <div class="agent__name">Maren Delacroix Vance</div>
    <div class="agent__title">Real Estate Broker</div>
  </div>

  <div class="divider"></div>

  <ul class="contact">
    <li>
      <svg viewBox="0 0 16 16" aria-hidden="true"><path d="M2 5c0-2 2-3 6-3s6 1 6 3v1h-3V5H5v1H2zM4 7h8l2 7H2z"/></svg>
      +1 225-555-0142
    </li>
    <li>
      <svg viewBox="0 0 16 16" aria-hidden="true"><path d="M1 3h14v10H1zM2 4.5v.6l6 4 6-4v-.6z" fill-rule="evenodd"/></svg>
      maren@riverhomesearch.com
    </li>
    <li>
      <svg viewBox="0 0 16 16" aria-hidden="true"><path d="M8 1a7 7 0 1 0 0 14A7 7 0 0 0 8 1zm0 1.5c.8 0 1.7 1.8 1.9 4.5H6.1C6.3 4.3 7.2 2.5 8 2.5zM2.6 7h2.2c.1-1.8.5-3.3 1-4A5.6 5.6 0 0 0 2.6 7zm8.6 0h2.2a5.6 5.6 0 0 0-3.2-4c.5.7.9 2.2 1 4zM2.6 9a5.6 5.6 0 0 0 3.2 4c-.5-.7-.9-2.2-1-4zm3.5 0c.2 2.7 1.1 4.5 1.9 4.5s1.7-1.8 1.9-4.5zm5.1 0c-.1 1.8-.5 3.3-1 4a5.6 5.6 0 0 0 3.2-4z"/></svg>
      www.riverhomesearch.com
    </li>
  </ul>

  <address class="address">4120 Magnolia HWY<br>Riverbend, LA, US 70999</address>

  <div class="edge-strip"></div>
</section>

</body>
</html>
```